Redesign current business card for food company

i would like to redesign my business card. our company is food company, our product range from chips, juices, milk and etc (mostly dried food stuff).
I want o keep same logo but , the rest is open to new design.
you can check at our website about our company www.orvelpantry.com

Target Market(s)

most of food company

Industry/Entity Type

Business

Contact Information for Business Card

I want to keep more to blue color...

Colors
3176b5
abd036

Requirements
Must have
• our old logo
Nice to have
• we do not mind to have nice material on bus card in order to accomplish nice design. for example: using spot uv, embossed and etc.

```html
<!DOCTYPE html>
<html lang="en">
<head>
<meta charset="utf-8">
<title>Orvel Pantry business card</title>
<link rel="stylesheet" href="https://fonts.googleapis.com/css2?family=Source+Sans+3:wght@400;600&display=swap">
<style>
  :root {
    --backdrop: #3b3430;
    --card: #141414;
    --card-edge: #222;
    --ink-light: #e6e6e6;
    --ink-muted: #a9a9a9;
    --brand-blue: #3176b5;
    --name-blue: #2f6fe0;
    --brand-green: #abd036;
    --title-green: #2fb34a;
    --rule: #5a5a5a;
  }
  * { box-sizing: border-box; margin: 0; padding: 0; }
  html, body { width: 1200px; height: 814px; overflow: hidden; }
  body {
    background: var(--backdrop);
    font-family: "Source Sans 3", sans-serif;
    position: relative;
  }
  .card {
    position: absolute;
    top: 252px;
    width: 540px;
    height: 309px;
    background: var(--card);
    border: 1px solid var(--card-edge);
  }
  .card--back { left: 40px; }
  .card--front { left: 620px; }

  .back-wordmark {
    position: absolute;
    left: 0; right: 0; top: 104px;
    text-align: center;
    font-size: 44px;
    font-weight: 600;
    color: #d8d8d8;
    letter-spacing: 1px;
  }
  .back-url {
    position: absolute;
    left: 0; right: 0; top: 196px;
    text-align: center;
    font-size: 14px;
    letter-spacing: 3px;
    color: var(--ink-muted);
  }

  .front-wordmark {
    position: absolute;
    right: 58px; top: 44px;
    font-size: 58px;
    font-weight: 600;
    color: var(--brand-blue);
    letter-spacing: 1px;
  }
  .holder {
    position: absolute;
    left: 40px; top: 62px;
  }
  .holder-name {
    font-size: 20px;
    font-weight: 600;
    color: var(--name-blue);
    line-height: 1.1;
  }
  .holder-title {
    font-size: 14px;
    font-weight: 600;
    color: var(--title-green);
  }
  .rule {
    position: absolute;
    height: 1px;
    background: var(--rule);
  }
  .rule--top { left: 40px; right: 40px; top: 116px; }
  .rule--bottom { left: 300px; right: 40px; top: 222px; }
  .contact-list {
    position: absolute;
    left: 40px; top: 126px;
    list-style: none;
  }
  .contact-list li {
    display: flex;
    align-items: center;
    gap: 8px;
    font-size: 15px;
    color: var(--ink-light);
    line-height: 22px;
  }
  .contact-list svg { width: 12px; height: 12px; fill: var(--name-blue); flex: none; }
  .address {
    position: absolute;
    right: 40px; top: 232px;
    text-align: right;
    font-size: 15px;
    line-height: 19px;
    color: var(--ink-light);
  }
  .address .url { letter-spacing: 1px; }
</style>
</head>
<body>
  <section class="card card--back" aria-label="Card back">
    <div class="back-wordmark">orvel</div>
    <div class="back-url">www.orvelpantry.com</div>
  </section>

  <section class="card card--front" aria-label="Card front">
    <div class="front-wordmark">orvel</div>
    <div class="holder">
      <div class="holder-name">Marcus Delaney</div>
      <div class="holder-title">President</div>
    </div>
    <div class="rule rule--top"></div>
    <ul class="contact-list">
      <li>
        <svg viewBox="0 0 12 12" aria-hidden="true"><path d="M2.5 0.5 L4.5 0.5 L5 3.2 L3.7 4.2 Q4.8 6.8 7.6 8.1 L8.7 6.9 L11.5 7.4 L11.5 9.6 Q11.5 11.5 9.5 11.5 Q0.5 10.5 0.5 2.5 Q0.5 0.5 2.5 0.5 Z"/></svg>
        555 210 4830
      </li>
      <li>
        <svg viewBox="0 0 12 12" aria-hidden="true"><path d="M3 0 H9 Q10 0 10 1 V11 Q10 12 9 12 H3 Q2 12 2 11 V1 Q2 0 3 0 Z M3.2 1.5 V9.5 H8.8 V1.5 Z"/></svg>
        555 372 9104
      </li>
      <li>
        <svg viewBox="0 0 12 12" aria-hidden="true"><path d="M3 0 H9 V3.5 H11 Q12 3.5 12 4.5 V10 Q12 11 11 11 H1 Q0 11 0 10 V4.5 Q0 3.5 1 3.5 H3 Z M4 1 V4.5 H8 V1 Z M2 7 V8 H10 V7 Z"/></svg>
        555 210 4831
      </li>
      <li>
        <svg viewBox="0 0 12 12" aria-hidden="true"><path d="M0 2 H12 V10 H0 Z M1 3 L6 7 L11 3 Z" fill-rule="evenodd"/></svg>
        marcus@orvelpantry.com
      </li>
    </ul>
    <div class="rule rule--bottom"></div>
    <address class="address" style="font-style:normal">
      1847 Linden St.<br>
      Harlow CA 90412<br>
      <span class="url">www.orvelpantry.com</span>
    </address>
  </section>
</body>
</html>
```